10-year customer thank you card

We want a greeting card that our sales reps can send to companies/customers who have been with our company for 10 or more years. We're a software company, our corporate color is blue but we also like green, orange, and purple. We'd like something rather minimal/simplistic for this card, perhaps building off our tree logo. We're really open to ideas for this one. You must use the template files that are uploaded. Copy included in 10 year thank you card file; the copy may change based on how it looks when laid out
Updates

I updated our brief. We'd prefer a sans serif font. I also uploaded a blank infographic image that includes more of our approved colors.

Industry/Entity Type

Software

Font styles to use
Sans Serif

```html
<!DOCTYPE html>
<html lang="en">
<head>
<meta charset="utf-8">
<title>10 Years – Thank You Card</title>
<link rel="stylesheet" href="https://fonts.googleapis.com/css2?family=Arimo:wght@400;700&display=swap">
<style>
  :root {
    --paper: #f9fafc;
    --rule: #1b1b1b;
    --brand-blue: #0a7fc2;
    --link-blue: #1a7fc4;
    --ink-dark: #2b2b2b;
    --teal: #41bdc5;
    --teal-shadow: #2fa2b3;
    --white: #ffffff;
  }
  * { box-sizing: border-box; margin: 0; padding: 0; }
  html, body {
    width: 869px;
    height: 1200px;
    overflow: hidden;
    background: var(--paper);
    font-family: "Arimo", Arial, sans-serif;
  }
  .card {
    position: relative;
    width: 869px;
    height: 1200px;
    overflow: hidden;
  }

  /* Inside-back half, printed upside down for folding */
  .back-half {
    position: absolute;
    left: 0; top: 0;
    width: 869px; height: 600px;
    background: var(--paper);
    transform: rotate(180deg);
  }
  .back-footer {
    position: absolute;
    left: 43px; right: 43px;
    bottom: 528px;
    height: 58px;
    border-top: 2px solid var(--rule);
    display: flex;
    justify-content: space-between;
    align-items: center;
  }
  .company-name {
    font-size: 21px;
    color: var(--ink-dark);
    font-weight: 400;
  }
  .web-address {
    font-size: 24px;
    color: var(--link-blue);
    font-weight: 400;
  }

  /* Front cover */
  .front-half {
    position: absolute;
    left: 0; top: 600px;
    width: 869px; height: 600px;
    background: var(--teal);
  }
  .front-art {
    position: absolute;
    inset: 0;
  }
  .years-badge {
    position: absolute;
    left: 679px; top: 23px;
    width: 158px; height: 185px;
    border: 2px solid var(--white);
    color: var(--white);
    text-align: center;
  }
  .years-number {
    display: block;
    font-size: 112px;
    line-height: 1;
    margin-top: 8px;
    letter-spacing: -2px;
  }
  .years-label {
    display: block;
    margin: 8px 10px 0;
    border-top: 2px solid var(--white);
    padding-top: 4px;
    font-size: 37px;
    line-height: 1.1;
  }
  .brand-mark {
    position: absolute;
    left: 275px; top: 95px;
    width: 352px; height: 352px;
    border-radius: 50%;
    background: var(--brand-blue);
    display: flex;
    align-items: center;
    justify-content: center;
    color: var(--white);
    font-size: 30px;
    font-weight: 700;
    text-align: center;
    line-height: 1.2;
  }
  .thank-you {
    position: absolute;
    left: 0; right: 0;
    top: 460px;
    text-align: center;
    color: var(--white);
    font-size: 70px;
    font-weight: 400;
    line-height: 1;
  }
</style>
</head>
<body>
  <main class="card">
    <section class="back-half">
      <footer class="back-footer">
        <span class="company-name">Northgrove Software</span>
        <span class="web-address">www.northgrovesoft.com</span>
      </footer>
    </section>

    <section class="front-half">
      <svg class="front-art" width="869" height="600" viewBox="0 0 869 600" aria-hidden="true">
        <polygon class="badge-shadow" points="679,208 837,208 837,23 869,71 869,493" fill="var(--teal-shadow)"/>
        <polygon class="title-shadow" points="290,540 610,540 700,600 350,600" fill="var(--teal-shadow)"/>
      </svg>

      <div class="years-badge">
        <span class="years-number">10</span>
        <span class="years-label">YEARS</span>
      </div>

      <div class="brand-mark">Northgrove<br>Software</div>

      <h1 class="thank-you">Thank You</h1>
    </section>
  </main>
</body>
</html>
```